Website Design for R W Builders: Showcasing Excellence in General Contracting

R W Builders, a leading general contractor based in California, is seeking a professional and engaging website design to effectively showcase our expertise, services, and commitment to excellence. The website will serve as a digital platform to represent our brand identity, highlight our portfolio, and attract potential clients in various sectors.

Key Objectives:

Reflect Company Identity: The website should accurately reflect the identity and values of R W Builders, including our dedication to quality, professionalism, and client satisfaction.
Showcase Services: Highlight our wide range of general contracting services, including but not limited to construction management, design-build, renovation, and commercial construction.
Portfolio Display: Display an extensive portfolio of past projects completed by R W Builders, showcasing our capabilities, craftsmanship, and successful outcomes.
Client Testimonials: Incorporate client testimonials and case studies to demonstrate our track record of delivering projects on time, within budget, and to the highest standards.
Contact Information: Ensure easy access to contact information, including phone number, email, and physical address, to facilitate communication with potential clients.
Responsive Design: Develop a responsive website design optimized for various devices and screen sizes, ensuring a seamless user experience across desktops, laptops, tablets, and smartphones.
Search Engine Optimization (SEO): Implement SEO best practices to enhance the visibility of the website on search engines, increasing organic traffic and generating leads.
User-Friendly Navigation: Create an intuitive and user-friendly navigation structure that enables visitors to easily find the information they need, such as services, portfolio, testimonials, and contact details.
Visual Appeal: Utilize visually appealing graphics, images, and layout designs to capture the attention of visitors and leave a lasting impression of professionalism and quality.
Compliance and Security: Ensure compliance with industry standards and regulations, as well as implementing necessary security measures to protect user data and privacy.

```html
<!DOCTYPE html>
<html lang="en">
<head>
<meta charset="utf-8">
<title>R W Builders — General Contracting</title>
<link href="https://fonts.googleapis.com/css2?family=Open+Sans:wght@400;600;700&family=Lato:wght@400;700&family=Oswald:wght@300;400&display=swap" rel="stylesheet">
<style>
:root{
  --orange:#f57c12;
  --orange-light:#f9a447;
  --ink:#111111;
  --text:#444444;
  --muted:#5b5b5b;
  --paper:#ffffff;
  --gray-band:#f1f1f1;
  --footer:#f4f4f4;
}
*{margin:0;padding:0;box-sizing:border-box}
html,body{width:1200px;height:3186px;overflow:hidden;background:var(--paper)}
body{position:relative;font-family:"Lato",sans-serif;color:var(--text)}
.abs{position:absolute}

/* nav */
.site-nav{position:absolute;left:0;top:0;width:1200px;height:73px;background:var(--paper);font-family:"Open Sans",sans-serif;font-size:15px;color:#222}
.site-nav a{position:absolute;top:26px;text-decoration:none;color:#222}
.brand-badge{position:absolute;left:525px;top:0;width:150px;height:146px;z-index:3}
.brand-badge span{position:absolute;left:0;width:150px;top:50px;text-align:center;font-family:"Open Sans",sans-serif;font-weight:700;font-size:19px;color:var(--ink);line-height:1.15}

/* hero */
.hero{position:absolute;left:0;top:73px;width:1200px;height:507px;background:linear-gradient(90deg,#1f1f1f 0%,#3a3632 45%,#4a4540 56%)}
.hero-photo{position:absolute;left:677px;top:0;width:523px;height:507px;background:linear-gradient(135deg,#e9e9e2 0%,#d8cf48 35%,#c2b52a 65%,#7d7a5e 100%)}
.hero-copy{position:absolute;left:99px;top:105px;width:480px;color:#fff}
.hero-copy .welcome{font-family:"Open Sans",sans-serif;font-weight:600;font-size:35px;line-height:1}
.hero-copy h1{font-family:"Open Sans",sans-serif;font-weight:700;font-size:53px;line-height:1;margin-top:22px;letter-spacing:.5px}
.hero-copy p{font-size:15.5px;line-height:26px;margin-top:26px}
.btn{position:absolute;display:block;height:44px;width:161px;background:var(--orange);color:#fff;font-family:"Lato",sans-serif;font-weight:700;font-size:14px;line-height:44px;padding-left:15px;text-decoration:none;border-radius:3px}
.btn::after{content:"";position:absolute;right:0;top:0;width:40px;height:44px;background:var(--orange-light);border-radius:0 3px 3px 0}
.btn svg{position:absolute;right:13px;top:13px;z-index:1}

/* section headings */
.section-title{font-family:"Open Sans",sans-serif;font-weight:600;font-size:39px;color:var(--ink);line-height:1}
.section-title em{font-style:normal;color:var(--orange)}
.title-rule{position:absolute;height:7px;border-top:3px solid var(--orange);border-bottom:2px solid var(--orange)}

/* service cards */
.service-card{position:absolute;top:797px;width:323px;height:437px}
.service-card .photo{position:absolute;left:0;top:0;width:323px;height:251px;clip-path:polygon(0 0,100% 0,100% 100%,50% 70%,0 100%)}
.service-card .badge{position:absolute;left:127px;top:165px;width:70px;height:70px;border-radius:50%;background:var(--ink)}
.service-card .badge.hot{background:var(--orange)}
.service-card .badge svg{position:absolute;left:19px;top:18px}
.service-card h3{position:absolute;left:0;top:257px;width:323px;text-align:center;font-family:"Open Sans",sans-serif;font-weight:600;font-size:21px;color:var(--ink)}
.service-card p{position:absolute;left:26px;top:301px;width:271px;text-align:center;font-family:"Oswald",sans-serif;font-weight:300;font-size:18px;line-height:25.5px;color:#333}
.service-card .rule{position:absolute;left:0;bottom:0;width:323px;height:4px;background:var(--ink)}
.service-card .rule.hot{background:var(--orange)}

/* about */
.about{position:absolute;left:0;top:1356px;width:1200px;height:629px;background:var(--gray-band)}
.about-art{position:absolute;left:0;top:54px;width:606px;height:538px;background:radial-gradient(ellipse at 55% 45%,#e08a3a 0%,#8fa3bd 45%,rgba(241,241,241,0) 75%)}
.about-copy{position:absolute;left:625px;top:68px;width:475px}
.about-copy h2{font-family:"Open Sans",sans-serif;font-weight:700;font-size:38px;line-height:41px;color:var(--ink)}
.about-copy h2 em{font-style:normal;color:var(--orange);display:block}
.about-copy p{font-size:14.8px;line-height:23.2px;color:var(--muted);margin-top:22px}
.about-copy p:first-of-type{margin-top:36px}

/* portfolio */
.portfolio-card{position:absolute;top:2204px;width:479px;height:474px}
.portfolio-card .photo{position:absolute;left:0;top:0;width:479px;height:374px;clip-path:polygon(0 0,100% 0,100% 100%,50% 60%,0 100%)}
.portfolio-card .badge{position:absolute;left:188px;top:250px;width:103px;height:103px;border-radius:50%;background:var(--ink)}
.portfolio-card .badge.hot{background:var(--orange)}
.portfolio-card .badge svg{position:absolute;left:28px;top:27px}
.portfolio-card h3{position:absolute;left:0;top:376px;width:479px;text-align:center;font-family:"Open Sans",sans-serif;font-weight:700;font-size:38px;color:var(--ink)}
.portfolio-card .rule{position:absolute;left:0;bottom:0;width:479px;height:5px;background:var(--ink)}
.portfolio-card .rule.hot{background:var(--orange)}

/* footer */
.site-footer{position:absolute;left:0;top:2798px;width:1200px;height:388px;background:var(--footer);font-family:"Open Sans",sans-serif}
.footer-brand{position:absolute;left:100px;top:120px;width:180px;text-align:center;font-weight:700;font-size:26px;color:var(--ink);line-height:1.2}
.footer-col{position:absolute;top:86px}
.footer-col h4{font-weight:700;font-size:20px;color:var(--ink);letter-spacing:.3px}
.footer-col h4::after{content:"";display:block;width:40px;height:3px;background:var(--ink);margin-top:10px}
.footer-col ul{list-style:none;margin-top:20px}
.footer-col li{position:relative;font-size:16px;color:#222;height:32px;line-height:22px;padding-left:23px}
.footer-col li::before{content:"";position:absolute;left:2px;top:6px;border-left:6px solid var(--ink);border-top:5px solid transparent;border-bottom:5px solid transparent}
.contact-line{position:absolute;font-size:15.5px;line-height:26px;color:#222;padding-left:29px}
.contact-line svg{position:absolute;left:0;top:4px}
.copyright{position:absolute;left:99px;top:343px;font-size:15px;color:#222}
</style>
</head>
<body>

<header class="site-nav">
  <a style="left:97px">Home</a>
  <a style="left:206px">Reflect Company</a>
  <a style="left:396px">Services</a>
  <a style="left:703px">Portfolio</a>
  <a style="left:834px">Client Testimonials</a>
  <a style="left:1034px">Conatact</a>
</header>
<div class="brand-badge">
  <svg width="150" height="146" viewBox="0 0 150 146"><polygon points="0,0 150,0 150,108 75,146 0,108" fill="#fff"/></svg>
  <span>R W<br>Builders</span>
</div>

<section class="hero">
  <div class="hero-photo" role="img" aria-label="Two engineers in hard hats and hi-vis jackets reviewing plans on a laptop"></div>
  <div class="hero-copy">
    <div class="welcome">WELCOME TO</div>
    <h1>R W BUILDERS</h1>
    <p>R W Builders, a leading general contractor based in California, is seeking a professional and engaging website design to effectively showcase our expertise, services, and commitment to excellence.</p>
  </div>
  <a class="btn" style="left:99px;top:325px">GET STARTED<svg width="12" height="18"><polygon points="0,0 12,9 0,18" fill="#fff"/></svg></a>
</section>

<h2 class="section-title abs" style="left:99px;top:695px">OUR <em>SERVICES</em></h2>
<div class="title-rule" style="left:99px;top:742px;width:89px"></div>
<svg class="abs" style="left:1037px;top:699px" width="26" height="26" viewBox="0 0 26 26"><circle cx="13" cy="13" r="13" fill="#9a9a9a"/><path d="M15 7 L9 13 L15 19 M9 13 H19" stroke="#fff" stroke-width="3" fill="none"/></svg>
<svg class="abs" style="left:1078px;top:699px" width="26" height="26" viewBox="0 0 26 26"><circle cx="13" cy="13" r="13" fill="#f57c12"/><path d="M11 7 L17 13 L11 19 M17 13 H7" stroke="#fff" stroke-width="3" fill="none"/></svg>

<article class="service-card" style="left:99px">
  <div class="photo" role="img" aria-label="Orange hard hat resting on blueprints in a warm workshop" style="background:linear-gradient(160deg,#3a2414 0%,#8a5a2c 45%,#c98a3e 70%,#6b4a30 100%)"></div>
  <div class="badge"><svg width="32" height="34" viewBox="0 0 32 34" fill="none" stroke="#fff" stroke-width="2"><rect x="5" y="2" width="20" height="26" rx="2"/><path d="M9 9h12M9 14h12M9 19h8"/></svg></div>
  <h3>Site Work</h3>
  <p>Concept- Creating new or enhancing areas of a home in which you will spend your daily life is an important decision. Thus, building a solid, trusting relationship with your</p>
  <div class="rule"></div>
</article>
<article class="service-card" style="left:439px">
  <div class="photo" role="img" aria-label="Concrete being poured from a chute onto gravel" style="background:linear-gradient(160deg,#b9b3a6 0%,#8f8a80 45%,#6e6a63 100%)"></div>
  <div class="badge hot"><svg width="32" height="34" viewBox="0 0 32 34" fill="none" stroke="#fff" stroke-width="2"><rect x="4" y="4" width="24" height="26"/><path d="M9 25 L23 9 M9 12v13h13"/></svg></div>
  <h3>Concrete</h3>
  <p>The primary bathroom was outdated with standard builder-grade tile, a single-person shower, and a jacuzzi tub that took up valuable square footage. The master</p>
  <div class="rule hot"></div>
</article>
<article class="service-card" style="left:781px">
  <div class="photo" role="img" aria-label="Worker laying sod beside a brick paver path" style="background:linear-gradient(160deg,#7c8a60 0%,#5c7a3a 45%,#a88a6e 100%)"></div>
  <div class="badge"><svg width="32" height="34" viewBox="0 0 32 34" fill="none" stroke="#fff" stroke-width="2"><path d="M6 30V14h8V6h6v24M3 30h26M9 18h2M9 23h2M16 11h2M16 16h2M16 21h2"/></svg></div>
  <h3>Landscaping</h3>
  <p>Interior Decorating provides you with cosmetic updates and a detailed resource list to transform your space without any structural changes.</p>
  <div class="rule"></div>
</article>

<section class="about">
  <div class="about-art" role="img" aria-label="Watercolour illustration of construction cranes, building frames and two workers"></div>
  <div class="about-copy">
    <h2>ABOUT<em>R W BUILDERS</em></h2>
    <p>With vast experience in the trades, site superintendence, safety, quality control, and all aspects of general contracting, R W Builders can plan, manage and execute building construction projects in all sizes under any delivery method: design-build, CM at Risk, or design-bid-build.</p>
    <p>R W Builders engages in horizontal construction (NAICS 237990) primarily with the county, state, public work, and federal municipalities under Job Order (JOC) type contracting vehicles. This requires emphasis on customer service, reasonable “best value” cost estimating, quality in construction, and safety on the site.</p>
  </div>
  <a class="btn" style="left:625px;top:465px">READ MORE<svg width="12" height="18"><polygon points="0,0 12,9 0,18" fill="#fff"/></svg></a>
</section>

<h2 class="section-title abs" style="left:0;width:1200px;text-align:center;top:2100px">OUR <em>PORTFOLIO</em></h2>
<div class="title-rule" style="left:556px;top:2148px;width:89px"></div>

<article class="portfolio-card" style="left:99px">
  <div class="photo" role="img" aria-label="Workers in hi-vis vests in front of scaffolding on a building site" style="background:linear-gradient(160deg,#c9b8a0 0%,#8a6a4a 40%,#5a5048 75%,#9a8a70 100%)"></div>
  <div class="badge"><svg width="48" height="50" viewBox="0 0 32 34" fill="none" stroke="#fff" stroke-width="1.6"><rect x="5" y="2" width="20" height="26" rx="2"/><path d="M9 9h12M9 14h12M9 19h8"/></svg></div>
  <h3>Past Projects</h3>
  <div class="rule"></div>
</article>
<article class="portfolio-card" style="left:621px">
  <div class="photo" role="img" aria-label="Finished bathroom with vanity blending into a line sketch of a shower" style="background:linear-gradient(120deg,#b8ada0 0%,#d8d2c8 45%,#f2f2f0 75%,#ffffff 100%)"></div>
  <div class="badge hot"><svg width="48" height="50" viewBox="0 0 32 34" fill="none" stroke="#fff" stroke-width="1.6"><rect x="4" y="4" width="24" height="26"/><path d="M9 25 L23 9 M9 12v13h13"/></svg></div>
  <h3>Completed Projects</h3>
  <div class="rule hot"></div>
</article>

<footer class="site-footer">
  <div class="footer-brand">R W<br>Builders</div>
  <div class="footer-col" style="left:351px">
    <h4>QUICK MENU</h4>
    <ul><li>About</li><li>Portfolio</li><li>Our Services</li><li>FAQs</li><li>Contact</li></ul>
  </div>
  <div class="footer-col" style="left:565px">
    <h4>WHAT WE DO</h4>
    <ul><li>Kitchen Design</li><li>Kitchen Remodeling</li><li>Bathroom Design</li><li>Bathroom Remodeling</li><li>Office</li></ul>
  </div>
  <div class="footer-col" style="left:795px">
    <h4>CONTACT US</h4>
  </div>
  <div class="contact-line" style="left:795px;top:153px"><svg width="14" height="18" viewBox="0 0 14 18"><path d="M7 1a6 6 0 0 1 6 6c0 4-6 10-6 10S1 11 1 7a6 6 0 0 1 6-6z" fill="#222"/><circle cx="7" cy="7" r="2.2" fill="#f4f4f4"/></svg>418 Oakridge Lane, Millbrook Falls,<br>California 95012, United States</div>
  <div class="contact-line" style="left:795px;top:232px"><svg width="16" height="16" viewBox="0 0 16 16"><path d="M3 1l3 3-2 2c1 2 3 4 5 5l2-2 3 3-2 3C7 15 1 9 1 3z" fill="#222"/></svg>+1 805-555-0142</div>
  <div class="contact-line" style="left:795px;top:283px;padding-left:35px"><svg width="20" height="15" viewBox="0 0 20 15" fill="none" stroke="#222" stroke-width="1.6"><rect x="1" y="1" width="18" height="13" rx="1"/><path d="M1 2l9 7 9-7"/></svg>info@rwbuilders.com</div>
  <div class="copyright">© copyrights 2024 © R W Builders |  All Rights Reserved</div>
</footer>

</body>
</html>
```